Redesign of outdated "Automotive Automation Company"

We are looking to finally update our outdated website with some cutting edge graphics. We want our customers to know we value technology and are cutting edge as far as design. We provide automation solutions for the automotive industry which essentially means we program robots, and sell automation related products.

Current URL

http://lnk.qorvi.example/Tm4pzr
Updates

Project Deadline Extended
Reason: The client portal wasn't working, it's just finally been fixed by Pixel Harbor. I will go through and start reviewing designs.

We are trying to go with the same look and feel on our business cards, line cards, apparel, etc. so we are forming a brand. I have included the current draft of the line card. Please utilize our newest Logo VEL Standardized Logo.jpg http://img.plomtra.example/zuKe9rb.jpg?1 Also we are trying hard to sell the following software / hardware companies so we can put some emphasis on their product. Corvane Systems https://www.corvanesystems.example/ We make money on selling the software and then on the integration. I think you should tie in this animation. ยท Shop Line Muddle to Momentum https://media.vuntelo.example/clips/9b2e7f1d04c3a85e6f2d1b7c9a0e4f3d8c6b2a1e.jpg?image_play_button=true&image_play_button_color=7b796ae0&image_crop_resized=275x155 In this 2-minute video, discover how Trellan can help run your plant floor. We are Authorized Integrators / Resellers for Pembry Controls Hadrix Sensorik http://hadrix.example/en/usa/ Corvane Systems https://www.corvanesystems.example/ Unified Motion Works www.umwkq.example Brisk Beltway Corp www.briskbeltway.example Castmere Fabrication http://www.castmerefab.example/strategic_partners.aspx

Target Market(s)

Large automotive companies looking for automation or robotic programming. So Professional is key.

Industry/Entity Type

Automotive

Font styles to use
Other font styles liked:
• Possible Open Sans or Lato

Colors
0591cc
ceeaf6
fbd4d5
fbf289
fece3e

Requirements
Must have
• Professional Modern Design.

I want a homepage design, and a rough Sales Page... Where numerous products can be listed.
Nice to have
• Maybe an updated logo if possible.

```html
<!DOCTYPE html>
<html lang="en">
<head>
<meta charset="utf-8">
<title>VEL Engineering Solutions</title>
<link href="https://fonts.googleapis.com/css2?family=Open+Sans:wght@300;400;600;700&display=swap" rel="stylesheet">
<style>
:root{
  --brand:#0591cc;
  --brand-bright:#1aa3d3;
  --ink:#333;
  --muted:#666;
  --line:#e4e4e4;
  --soft:#f8f8f8;
  --band:#f2f2f2;
  --green:#6ab83a;
  --red:#e2154a;
  --footer:#262626;
  --footer-text:#9a9a9a;
}
*{margin:0;padding:0;box-sizing:border-box}
html,body{width:1200px;height:2228px;overflow:hidden}
body{position:relative;background:#fff;font-family:'Open Sans',Arial,sans-serif;color:var(--ink)}
.abs{position:absolute}

/* header */
.site-header{position:absolute;left:0;top:0;width:1200px;height:141px;background:#fff}
.brand-name{left:97px;top:38px;font-size:22px;font-weight:700;color:var(--brand);letter-spacing:1px}
.brand-tag{left:97px;top:72px;font-size:10px;color:var(--muted);letter-spacing:1px;text-transform:uppercase}
.social-dot{width:26px;height:26px;border-radius:50%;background:#c9c9c9;top:29px}
.call-icon{left:942px;top:23px;width:38px;height:38px;border-radius:50%;border:1px solid var(--line);display:flex;align-items:center;justify-content:center}
.call-label{left:995px;top:23px;font-size:13px;color:#777;letter-spacing:.5px}
.call-number{left:995px;top:44px;font-size:13px;color:var(--brand);letter-spacing:.5px}
.main-nav a{position:absolute;top:96px;font-size:13px;color:#333;text-decoration:none;text-transform:uppercase}
.main-nav .active{left:462px;top:89px;width:75px;height:36px;border:1px solid var(--brand-bright);border-radius:3px;color:var(--brand);text-align:center;line-height:34px}
.nav-divider{top:94px;width:1px;height:26px;background:#eee}

/* hero */
.hero{left:0;top:141px;width:1200px;height:527px;background:linear-gradient(180deg,#9ea3a5,#7d8386 55%,#b7babb)}
.hero-title{left:0;top:226px;width:1200px;text-align:center;font-size:46px;font-weight:700;color:#fff;text-shadow:0 2px 4px rgba(0,0,0,.5)}
.hero-sub{left:0;top:296px;width:1200px;text-align:center;font-size:18px;color:#fff;letter-spacing:.5px;text-shadow:0 1px 3px rgba(0,0,0,.5)}
.hero-arrow{top:268px;width:34px;height:34px;border-radius:50%;background:rgba(0,0,0,.7);display:flex;align-items:center;justify-content:center}

/* services */
.services{left:0;top:668px;width:1200px;height:430px;background:var(--soft);border-bottom:1px solid var(--line)}
.section-title{font-size:28px;font-weight:400;color:#333}
.section-sub{font-size:15px;color:#555}
.mini-arrow{top:32px;width:26px;height:26px;border-radius:50%;border:1px solid #ccc;background:#fff;display:flex;align-items:center;justify-content:center}
.service-icon{width:72px;height:72px;border-radius:50%;background:var(--brand-bright);display:flex;align-items:center;justify-content:center}
.service-name{font-size:13px;color:#333;text-transform:uppercase}
.service-text{font-size:11.5px;line-height:20px;color:#666;width:200px}
.col-divider{width:1px;height:110px;background:#ececec}

/* about */
.about-heading{left:97px;top:1144px;width:260px;font-size:15px;line-height:24px;color:#222;text-transform:uppercase}
.about-copy{left:97px;top:1207px;width:250px;font-size:11.5px;line-height:21px;color:#444}
.btn-more{left:98px;top:1432px;width:102px;height:33px;background:var(--brand-bright);color:#fff;font-size:11px;text-transform:uppercase;display:flex;align-items:center;justify-content:center;border-radius:2px}
.feature-card{top:1152px;width:225px;height:313px;background:#f7f7f7;border:1px solid #eee}
.feature-card .head{height:62px;padding:12px 20px;color:#fff;font-size:13px;line-height:22px;text-transform:uppercase}
.feature-card .photo{height:163px}
.feature-card p{padding:14px 12px;font-size:11.5px;line-height:20px;color:#666;text-align:center}

/* testimonials */
.testimonials{left:0;top:1518px;width:1200px;height:252px;background:var(--band)}
.quote-text{left:170px;top:95px;width:860px;text-align:center;font-size:12.5px;line-height:22px;color:#555}
.quote-mark{font-size:40px;color:#999;font-family:Georgia,serif}
.avatar{left:532px;top:1697px;width:136px;height:136px;border-radius:50%;border:6px solid #fff;background:linear-gradient(160deg,#8aa0b3,#3e4d5c);box-shadow:0 0 0 1px #ddd}
.partner{top:1872px;font-size:22px;font-weight:600;display:flex;align-items:center;gap:8px}

/* footer */
.site-footer{left:0;top:1943px;width:1200px;height:285px;background:var(--footer)}
.foot-head{top:38px;font-size:14px;color:#ddd;text-transform:uppercase;letter-spacing:.5px}
.foot-text{font-size:11.5px;line-height:20px;color:var(--footer-text)}
.foot-row{display:flex;gap:14px;align-items:flex-start}
.copyright{left:0;top:246px;width:1200px;text-align:center;font-size:11px;color:#aaa}
.copyright span{color:var(--brand-bright)}
</style>
</head>
<body>

<header class="site-header">
  <div class="abs brand-name">VEL ENGINEERING SOLUTIONS</div>
  <div class="abs brand-tag">Automation • Robotics • Controls</div>

  <span class="abs social-dot" style="left:806px"></span>
  <span class="abs social-dot" style="left:836px"></span>
  <span class="abs social-dot" style="left:866px"></span>

  <div class="abs call-icon">
    <svg width="16" height="16" viewBox="0 0 24 24"><path d="M6.6 10.8a15.1 15.1 0 006.6 6.6l2.2-2.2c.3-.3.7-.4 1-.2 1.1.4 2.3.6 3.6.6.6 0 1 .4 1 1V20c0 .6-.4 1-1 1A17 17 0 013 4c0-.6.4-1 1-1h3.5c.6 0 1 .4 1 1 0 1.3.2 2.5.6 3.6.1.3 0 .7-.2 1z" fill="#0591cc"/></svg>
  </div>
  <div class="abs call-label">CALL US</div>
  <div class="abs call-number">1-855-555-0142</div>

  <nav class="main-nav">
    <a class="active">Home</a>
    <a style="left:577px">About Us</a>
    <span class="abs nav-divider" style="left:672px"></span>
    <a style="left:697px">Our Services</a>
    <span class="abs nav-divider" style="left:815px"></span>
    <a style="left:845px">News</a>
    <span class="abs nav-divider" style="left:907px"></span>
    <a style="left:937px">Contact Us</a>
    <span class="abs nav-divider" style="left:1045px"></span>
    <a style="left:1071px">FAQ</a>
  </nav>
</header>

<section class="abs hero" role="img" aria-label="Team of business people assembling large gear wheels">
  <div class="abs hero-title">VEL ENGINEERING SOLUTIONS</div>
  <div class="abs hero-sub">AUTOMATION &nbsp;•&nbsp; ROBOTICS &nbsp;•&nbsp; CONTROLS</div>
  <span class="abs hero-arrow" style="left:35px"><svg width="12" height="12" viewBox="0 0 12 12"><path d="M8 1L3 6l5 5" stroke="#fff" stroke-width="2" fill="none"/></svg></span>
  <span class="abs hero-arrow" style="left:1131px"><svg width="12" height="12" viewBox="0 0 12 12"><path d="M4 1l5 5-5 5" stroke="#fff" stroke-width="2" fill="none"/></svg></span>
</section>

<section class="abs services">
  <h2 class="abs section-title" style="left:97px;top:24px">Our Services</h2>
  <p class="abs section-sub" style="left:98px;top:68px">Bring our experts to your business</p>
  <span class="abs mini-arrow" style="left:1039px"><svg width="8" height="8" viewBox="0 0 8 8"><path d="M5.5 1L2.5 4l3 3" stroke="#555" stroke-width="1.4" fill="none"/></svg></span>
  <span class="abs mini-arrow" style="left:1075px"><svg width="8" height="8" viewBox="0 0 8 8"><path d="M2.5 1l3 3-3 3" stroke="#555" stroke-width="1.4" fill="none"/></svg></span>

  <span class="abs col-divider" style="left:413px;top:122px"></span>
  <span class="abs col-divider" style="left:786px;top:122px"></span>
  <span class="abs col-divider" style="left:413px;top:285px"></span>
  <span class="abs col-divider" style="left:786px;top:285px"></span>

  <!-- row 1 -->
  <div class="abs service-icon" style="left:97px;top:143px"><svg width="30" height="30" viewBox="0 0 30 30"><rect x="6" y="8" width="18" height="12" rx="1" fill="none" stroke="#fff" stroke-width="2"/><path d="M3 23h24" stroke="#fff" stroke-width="2"/></svg></div>
  <div class="abs service-name" style="left:187px;top:138px">Applications Engineering</div>
  <div class="abs service-text" style="left:187px;top:162px">Provide electrical and mechanical expertise to solve automation specific application problems by</div>

  <div class="abs service-icon" style="left:466px;top:143px"><svg width="30" height="30" viewBox="0 0 30 30"><path d="M4 21a11 11 0 0122 0z" fill="#fff"/><path d="M15 20l5-7" stroke="#1aa3d3" stroke-width="2"/></svg></div>
  <div class="abs service-name" style="left:555px;top:138px">Controls Engineering</div>
  <div class="abs service-text" style="left:555px;top:162px">Provide electrical and mechanical expertise to solve automation specific application problems by</div>

  <div class="abs service-icon" style="left:818px;top:143px"><svg width="30" height="30" viewBox="0 0 30 30"><rect x="4" y="6" width="22" height="14" rx="1" fill="#fff"/><path d="M15 20v4M10 25h10" stroke="#fff" stroke-width="2"/></svg></div>
  <div class="abs service-name" style="left:907px;top:138px">Design Engineering</div>
  <div class="abs service-text" style="left:907px;top:162px">Provide electrical and mechanical expertise to solve automation specific application problems by</div>

  <!-- row 2 -->
  <div class="abs service-icon" style="left:97px;top:306px"><svg width="30" height="30" viewBox="0 0 30 30"><rect x="5" y="14" width="9" height="9" fill="none" stroke="#fff" stroke-width="2"/><rect x="16" y="14" width="9" height="9" fill="none" stroke="#fff" stroke-width="2"/><rect x="10.5" y="5" width="9" height="9" fill="none" stroke="#fff" stroke-width="2"/></svg></div>
  <div class="abs service-name" style="left:187px;top:301px">Design Specification</div>
  <div class="abs service-text" style="left:187px;top:325px">Provide electrical and mechanical expertise to solve automation specific application problems by</div>

  <div class="abs service-icon" style="left:466px;top:306px"><svg width="30" height="30" viewBox="0 0 30 30"><circle cx="12" cy="17" r="6" fill="none" stroke="#fff" stroke-width="3" stroke-dasharray="3 2"/><circle cx="21" cy="9" r="4" fill="none" stroke="#fff" stroke-width="2.5" stroke-dasharray="2 1.5"/></svg></div>
  <div class="abs service-name" style="left:555px;top:301px">Electrical Engineering</div>
  <div class="abs service-text" style="left:555px;top:325px">Provide electrical and mechanical expertise to solve automation specific application problems by</div>

  <div class="abs service-icon" style="left:818px;top:306px"><svg width="30" height="30" viewBox="0 0 30 30"><path d="M5 24V6M5 24h21" stroke="#fff" stroke-width="2" fill="none"/><path d="M8 20l6-6 4 4 7-8" stroke="#fff" stroke-width="2.2" fill="none"/></svg></div>
  <div class="abs service-name" style="left:907px;top:301px">Field Installation</div>
  <div class="abs service-text" style="left:907px;top:325px">Provide electrical and mechanical expertise to solve automation specific application problems by</div>
</section>

<section>
  <h3 class="abs about-heading">Helping your business optimize its automation....</h3>
  <p class="abs about-copy">Industrial Automation is constantly evolving with ever-changing technological break-throughs. For companies to remain competi-tive, they need to be more nimble than ever implementing productivity and manufacturing innovations. But identifying and implementing the right Automation, Robotics and industrial Controls is never easy. That's where our team of experts comes in to play bringing our proven experience to the table.</p>
  <div class="abs btn-more">Read more +</div>

  <article class="abs feature-card" style="left:379px">
    <div class="head" style="background:var(--green)">Get to know our team approach</div>
    <div class="photo" role="img" aria-label="Team members gathered around a whiteboard" style="background:linear-gradient(135deg,#e9ecef,#b9c0c6)"></div>
    <p>Lorem ipsum dolor sit amet, consecte-tur adipiscing elit. Sed blandit massa vel mauris sollicitudin dignissim.</p>
  </article>
  <article class="abs feature-card" style="left:627px">
    <div class="head" style="background:var(--red)">This way to automation success</div>
    <div class="photo" role="img" aria-label="White humanoid robot in profile" style="background:linear-gradient(135deg,#dfe6ea,#8d989f)"></div>
    <p>Lorem ipsum dolor sit amet, consecte-tur adipiscing elit. Sed blandit massa vel mauris sollicitudin dignissim.</p>
  </article>
  <article class="abs feature-card" style="left:876px">
    <div class="head" style="background:var(--brand-bright)">Bring great ideas to your business</div>
    <div class="photo" role="img" aria-label="Thoughtful woman in front of a chalkboard with question marks" style="background:linear-gradient(135deg,#c7c9c7,#7f8a6a)"></div>
    <p>Lorem ipsum dolor sit amet, consecte-tur adipiscing elit. Sed blandit massa vel mauris sollicitudin dignissim.</p>
  </article>
</section>

<section class="abs testimonials">
  <h2 class="abs section-title" style="left:0;top:22px;width:1200px;text-align:center">What our clients say</h2>
  <span class="abs quote-mark" style="left:138px;top:80px">“</span>
  <p class="abs quote-text">Lorem ipsum dolor sit amet, consectetur adipiscing elit, sed do eiusmod tempor incididunt ut labore et dolore magna aliqua. Ut enim ad minim veniam, quis nostrud exercitation ullamco laboris nisi ut aliquip ex ea commodo consequat. Duis aute irure dolor in reprehenderit in voluptate velit esse cillum dolore eu fugiat nulla pariatur. Excepteur sint occaecat cupidatat non</p>
  <span class="abs quote-mark" style="left:1030px;top:122px">”</span>
</section>
<div class="abs avatar" role="img" aria-label="Client portrait"></div>

<div class="abs partner" style="left:118px;color:#d4142a"><span style="width:12px;height:12px;background:#d4142a"></span>Hadrix Sensorik</div>
<div class="abs partner" style="left:434px;color:#4d7a3a"><span style="width:14px;height:14px;border-radius:50%;background:#4d7a3a"></span>Corvane Systems</div>
<div class="abs partner" style="left:630px;color:#b8232f;font-size:19px">Pembry Controls</div>
<div class="abs partner" style="left:822px;color:#555;font-size:19px">Sonavo</div>
<div class="abs partner" style="left:990px;color:#888"><span style="width:14px;height:14px;background:#888"></span>Kelvry</div>

<footer class="abs site-footer">
  <h4 class="abs foot-head" style="left:99px">Who we are</h4>
  <p class="abs foot-text" style="left:99px;top:70px;width:260px">Lorem ipsum dolor sit amet, consectetur adipiscing elit, sed do eiusmod tempor incididunt ut labore et dolore magna aliqua. Ut enim ad minim veniam, quis nostrud exercitation ullamco laboris Lorem ipsum dolor sit amet, consectetur adipiscing elit, sed do eiusmod tempor incididunt ut labore et</p>

  <h4 class="abs foot-head" style="left:411px">Latest tweet`s</h4>
  <div class="abs foot-row" style="left:413px;top:70px;width:240px">
    <span style="width:16px;height:16px;background:#ddd;border-radius:2px;flex:none;margin-top:2px"></span>
    <p class="foot-text">VEL now present our first Nimbusfront Template Tidecrest. See more here http://sh.example/Q4tLm2</p>
  </div>
  <div class="abs foot-row" style="left:413px;top:140px;width:240px">
    <span style="width:16px;height:16px;background:#ddd;border-radius:2px;flex:none;margin-top:2px"></span>
    <p class="foot-text">VEL now present our first Nimbusfront Template Tidecrest. See more here http://sh.example/Q4tLm2</p>
  </div>

  <h4 class="abs foot-head" style="left:693px">Contact us</h4>
  <div class="abs foot-row" style="left:693px;top:70px;width:260px">
    <svg width="14" height="18" viewBox="0 0 14 18" style="flex:none"><path d="M7 1a6 6 0 00-6 6c0 4.5 6 10 6 10s6-5.5 6-10a6 6 0 00-6-6z" fill="none" stroke="#aaa" stroke-width="1.4"/><circle cx="7" cy="7" r="2" fill="#aaa"/></svg>
    <p class="foot-text">Address: VEL Engineering, Alder Ridge 4C, 7710 Fenholt</p>
  </div>
  <div class="abs foot-row" style="left:693px;top:130px">
    <svg width="16" height="16" viewBox="0 0 24 24" style="flex:none"><path d="M6.6 10.8a15.1 15.1 0 006.6 6.6l2.2-2.2c.3-.3.7-.4 1-.2 1.1.4 2.3.6 3.6.6.6 0 1 .4 1 1V20c0 .6-.4 1-1 1A17 17 0 013 4c0-.6.4-1 1-1h3.5c.6 0 1 .4 1 1 0 1.3.2 2.5.6 3.6.1.3 0 .7-.2 1z" fill="none" stroke="#aaa" stroke-width="1.6"/></svg>
    <p class="foot-text">Phone: 1-855-555-0142</p>
  </div>
  <div class="abs foot-row" style="left:693px;top:160px">
    <svg width="16" height="12" viewBox="0 0 16 12" style="flex:none;margin-top:4px"><rect x=".7" y=".7" width="14.6" height="10.6" fill="none" stroke="#aaa" stroke-width="1.3"/><path d="M1 1l7 6 7-6" fill="none" stroke="#aaa" stroke-width="1.3"/></svg>
    <p class="foot-text">Email: info@velengsolutions.example</p>
  </div>

  <h4 class="abs foot-head" style="left:1000px">Social media</h4>
  <div class="abs foot-row" style="left:1000px;top:72px"><span style="width:7px;height:7px;background:#bbb;margin-top:7px"></span><p class="foot-text">Friendlane</p></div>
  <div class="abs foot-row" style="left:1000px;top:100px"><span style="width:7px;height:7px;background:#bbb;margin-top:7px"></span><p class="foot-text">Chirpline</p></div>
  <div class="abs foot-row" style="left:1000px;top:128px"><span style="width:7px;height:7px;background:#bbb;margin-top:7px"></span><p class="foot-text">Circleup</p></div>
  <div class="abs foot-row" style="left:1000px;top:156px"><span style="width:7px;height:7px;background:#bbb;margin-top:7px"></span><p class="foot-text">Vidstream</p></div>

  <div class="abs" style="left:0;top:222px;width:1200px;height:1px;background:#333"></div>
  <p class="abs copyright">©2013 - 2014 <span>VEL ENGINEERING SOLUTIONS INC.</span>, All Rights Reserved.</p>
</footer>

</body>
</html>
```